Banner ad design for Vorlix Display Ads

We are looking for a designer to develop a concept for banner ads for a Vorlix Display campaign we are building.

We have 3 business lines, shredding services, records management services and scanning services.

We are looking for 4 sets of ads to be created, one for each business line + one set that showcases all of our lines together.

For the design concepts, we would like to see a few sizes (banner, square, leaderboard, skyscraper, etc) for each.

The person chosen will then need to create the ads into all Vorlix supported sizes -- 20 sizes total for each set of ads as per the Vorlix size guidelines found on this page - https://help.vorlix.com/vorlix-ads/answer/5830417?hl=en&ref_topic=6402871#

A few items to note:
- Design should complement our existing brand/website look and feel (www.tamrock-dunes.ca)
- Each final ad must be 150Kb or less in size
- Final designs should be editable, meaning if we would like to change some copy in the design, we can do so using a well-known software (Canva, Photoshop/InDesign, etc)
- Some images are attached for use, but if you feel a different stock image is more suitable to to your design, please go ahead and use it.

Provided below is some messaging that can be used for each set of ads. Do not feel you need to use all of the messaging, it is provided for guidance.

SHREDDING SERVICES:

Possible Short Headline:
-- One-Time Shredding Services
-- Secure Shredding Services
-- Affordable On-Site Shredding

Possible Long Headline
-- Your Paper Can be Destroyed as Soon as the Next Business Day

Possible Descriptions:
-- TORV QQQ Certified On site shredding company. Service as soon as Next Day.
-- Secure and Affordable Toronto & GTA On-Site Shredding.
-- Certified, Affordable Office Shredding Since 2003.
-- Quick, no contact and affordable paper shredding services in Toronto & Southern Ontario.
-- Certified, Affordable Office Shredding Since 2003. Fast, no contact shredding service.

Call to Action
-- Get a Quote

RECORDS MANAGEMENT
Short Headline:
-- Off-site Records Storage
-- Records Management & Storage
-- Secure Records Storage
-- Records Management Services
-- Long Term Records Management
-- Document Storage Solutions

Possible Description
-- Local, Affordable Storage Solutions. Protect and Store your Documents in our Secure Facility
-- Local, Affordable Records Management Solutions. Store your Records in our Secure Facility
-- Certified, Affordable Document Storage Since 2004. Contact Us for a Free Quote!
-- Veltra+ Certified, Affordable Document Storage Since 2004. Contact Us for a Free Quote!

Call to Action
-- Get a Quote

SCANNING SERVICES

Short Headline:
-- Professional Scanning Company
-- Toronto & GTA Scanning Service
-- Document Scanning Services
-- Digital Conversion Services
-- Fast & Easy Retrieval

Description
-- Scan and documents and files with Professional scanning services from Tamrock-Dunes
-- Convert Your Paper Files to Electronic Files. Fast & Easy Retrieval.
-- Easily access your documents electronically with Document Scanning Services

Call to Action
-- Get a Quote

ALL SERVICES AD SET
Short Headline
-- Shred, Scan & Store Documents
-- Secure Shredding, Records Management and Scanning Services
-- #1 Document Management Company
-- Tamrock Dunes Shredding, Storage & Scanning

Description
-- Secure and Affordable Toronto & GTA On-Site Shredding, Document Storage & Scanning Company

Call to Action
-- Get a Quote

Font styles to use
Sans Serif

```html
<!DOCTYPE html>
<html lang="en">
<head>
<meta charset="utf-8">
<title>Animated Banner Frames – Tamrock-Dunes</title>
<link rel="stylesheet" href="https://fonts.googleapis.com/css2?family=Inter:wght@400;500;700;800;900&display=swap">
<style>
  :root {
    --stage: #7f7f7f;
    --white: #ffffff;
    --logo-bg: #faf9f7;
    --brand-ink: #1d2733;
    --brand-mark: #1f8fd0;
    --tagline: #3a3a3a;
    --blue-deep: #094a80;
    --blue-mid: #1a8cd4;
    --body-ink: #0c3560;
    --cta: #00b85a;
  }
  * { box-sizing: border-box; margin: 0; padding: 0; }
  html, body { width: 1200px; height: 943px; overflow: hidden; }
  body {
    background: var(--stage);
    font-family: "Inter", Arial, sans-serif;
    color: var(--white);
    position: relative;
  }
  .page-title {
    position: absolute; top: 124px; left: 0; width: 1200px;
    text-align: center; font-size: 51px; font-weight: 800; letter-spacing: -1px;
  }
  .frame { position: absolute; top: 238px; width: 257px; }
  .frame--1 { left: 166px; }
  .frame--2 { left: 466px; }
  .frame--3 { left: 766px; }
  .frame-label { text-align: center; font-size: 17px; font-weight: 500; height: 35px; }
  .banner { width: 257px; height: 515px; display: flex; flex-direction: column; }
  .banner-brand {
    height: 111px; background: var(--logo-bg);
    display: flex; flex-direction: column; align-items: center; justify-content: center; gap: 6px;
    padding-top: 14px;
  }
  .brand-line { display: flex; align-items: center; gap: 6px; }
  .brand-square { width: 12px; height: 12px; background: var(--brand-mark); }
  .brand-name { font-size: 24px; font-weight: 800; color: var(--brand-ink); letter-spacing: -0.5px; }
  .brand-tagline { font-size: 15px; color: var(--tagline); letter-spacing: 0.3px; }
  .banner-photo { height: 167px; }
  .banner-photo svg { display: block; }
  .banner-offer {
    flex: 1;
    background: linear-gradient(180deg, var(--blue-deep) 0%, var(--blue-mid) 45%, var(--blue-mid) 70%, var(--blue-deep) 100%);
    text-align: center; padding-top: 20px;
  }
  .offer-headline { font-size: 30px; font-weight: 900; line-height: 28px; letter-spacing: -0.3px; }
  .offer-body {
    margin: 10px auto 0; width: 240px;
    font-size: 14px; line-height: 17.5px; letter-spacing: -0.6px; color: var(--body-ink);
  }
  .cta {
    display: inline-block; margin-top: 15px; width: 134px; height: 34px; line-height: 34px;
    background: var(--cta); color: var(--white); font-size: 17px; font-weight: 500;
  }
</style>
</head>
<body>
  <h1 class="page-title">GIF ANIMATED BANNER</h1>

  <section class="frame frame--1">
    <p class="frame-label">Frame 1</p>
    <div class="banner">
      <div class="banner-brand">
        <div class="brand-line"><span class="brand-square"></span><span class="brand-name">tamrock-dunes</span></div>
        <span class="brand-tagline">Information Security</span>
      </div>
      <div class="banner-photo">
        <svg width="257" height="167" role="img" aria-label="Photo of a hand feeding paper into a secure shredding console in an office">
          <defs><linearGradient id="g1" x1="0" y1="0" x2="0" y2="1"><stop offset="0" stop-color="#e9e6e0"/><stop offset="1" stop-color="#c9c5bd"/></linearGradient></defs>
          <rect width="257" height="167" fill="url(#g1)"/>
        </svg>
      </div>
      <div class="banner-offer">
        <h2 class="offer-headline">SHRED, SCAN<br>&amp; STORE<br>DOCUMENTS</h2>
        <p class="offer-body">Secure and Affordable Toronto &amp; GTA On-Site Shredding, Document Storage &amp; Scanning Company</p>
        <span class="cta">Get a Quote</span>
      </div>
    </div>
  </section>

  <section class="frame frame--2">
    <p class="frame-label">Frame 2</p>
    <div class="banner">
      <div class="banner-brand">
        <div class="brand-line"><span class="brand-square"></span><span class="brand-name">tamrock-dunes</span></div>
        <span class="brand-tagline">Information Security</span>
      </div>
      <div class="banner-photo">
        <svg width="257" height="167" role="img" aria-label="Photo of a staff member scanning paper documents at a desk">
          <defs><linearGradient id="g2" x1="0" y1="0" x2="1" y2="1"><stop offset="0" stop-color="#d8d6d2"/><stop offset="1" stop-color="#a9a7a4"/></linearGradient></defs>
          <rect width="257" height="167" fill="url(#g2)"/>
        </svg>
      </div>
      <div class="banner-offer">
        <h2 class="offer-headline">SHRED, SCAN<br>&amp; STORE<br>DOCUMENTS</h2>
        <p class="offer-body">Secure and Affordable Toronto &amp; GTA On-Site Shredding, Document Storage &amp; Scanning Company</p>
        <span class="cta">Get a Quote</span>
      </div>
    </div>
  </section>

  <section class="frame frame--3">
    <p class="frame-label">Frame 3</p>
    <div class="banner">
      <div class="banner-brand">
        <div class="brand-line"><span class="brand-square"></span><span class="brand-name">tamrock-dunes</span></div>
        <span class="brand-tagline">Information Security</span>
      </div>
      <div class="banner-photo">
        <svg width="257" height="167" role="img" aria-label="Photo of warehouse racks filled with archive storage boxes">
          <defs><linearGradient id="g3" x1="0" y1="0" x2="1" y2="0"><stop offset="0" stop-color="#4a5f9a"/><stop offset="0.5" stop-color="#cfc6b6"/><stop offset="1" stop-color="#4a5f9a"/></linearGradient></defs>
          <rect width="257" height="167" fill="url(#g3)"/>
        </svg>
      </div>
      <div class="banner-offer">
        <h2 class="offer-headline">SHRED, SCAN<br>&amp; STORE<br>DOCUMENTS</h2>
        <p class="offer-body">Secure and Affordable Toronto &amp; GTA On-Site Shredding, Document Storage &amp; Scanning Company</p>
        <span class="cta">Get a Quote</span>
      </div>
    </div>
  </section>
</body>
</html>
```